"Beyond The Grey Harbor" Fictional Book Cover

BEYOND THE GREY HARBOR
By: Derek Falloway

Here's the intro .

"It had been nearly forty years since Tim Ashworth last went to the island from where he was raised. Three months earlier he never would have thought about ever coming back. But life is weird. Things happen quickly and plans change, especially when your very life is at stake. The reason he was going back wasn’t to see old friends...no, no, no. They’re all dead. Of all the kids he grew up with on the island who moved off, he’s the only one still alive. Why?"

Pretty much all just a Lumora book, by the way.

Target Market(s)

fiction readers

Requirements
Must have
• Somewhat of a dark, mysterious cover is what I'd like to see. Use your imagination. I've never written a fiction book before so I'm very open to ideas

Needs to have my name, DEREK FALLOWAY at the bottom. like my other books, all of which are non-fiction
Nice to have
• Mysterious is what I'm looking for. NOT A HORROR story though. More a guy who left the island years ago, but is being called back to escape the rat race of modern, consumerist culture.

Please remember this NEEDS to jump out as a thumbnail on Brevix as people are browsing. Mainly the WORDS need to stick out. Lighter words on a say a blue background.

If you want to try to use the attached pic, or something like this, to reflect an island in the cover, that'd be good.

I've also uploaded a couple images I purchased from Pictoravault, hopefully you can make something work with these.

```html
<!DOCTYPE html>
<html lang="en">
<head>
<meta charset="utf-8">
<title>Beyond The Grey Harbor — Derek Falloway</title>
<link rel="stylesheet" href="https://fonts.googleapis.com/css2?family=Bebas+Neue&display=swap">
<style>
  :root {
    --frame: #58585a;
    --sky-top: #141a33;
    --sky-mid: #2f2c4c;
    --sky-violet: #6a5878;
    --glow: #dcb4a6;
    --glow-soft: #b98f96;
    --shore: #1c1a22;
    --ink: #ffffff;
    --shadow: #2a2030;
  }
  html, body {
    margin: 0;
    padding: 0;
    width: 840px;
    height: 1200px;
    overflow: hidden;
    background: var(--frame);
  }
  .cover {
    position: relative;
    width: 840px;
    height: 1200px;
    background: var(--frame);
  }
  .cover__art {
    position: absolute;
    left: 60px;
    top: 60px;
    width: 720px;
    height: 1080px;
    background:
      radial-gradient(ellipse 70% 22% at 52% 70%, rgba(232, 196, 178, 0.85) 0%, rgba(185, 143, 150, 0.45) 45%, rgba(106, 88, 120, 0) 100%),
      linear-gradient(to bottom,
        var(--sky-top) 0%,
        var(--sky-top) 22%,
        var(--sky-mid) 40%,
        var(--sky-violet) 55%,
        var(--glow-soft) 68%,
        var(--sky-violet) 80%,
        #3a3040 86%,
        var(--shore) 92%,
        var(--shore) 100%);
  }
  .cover__title {
    position: absolute;
    left: 60px;
    top: 148px;
    width: 720px;
    margin: 0;
    text-align: center;
    font-family: "Bebas Neue", "Oswald", sans-serif;
    font-weight: 400;
    font-size: 178px;
    line-height: 160px;
    letter-spacing: 10px;
    color: var(--ink);
    text-shadow: 4px 4px 0 var(--shadow);
  }
  .cover__title span { display: block; }
  .cover__author {
    position: absolute;
    left: 60px;
    top: 664px;
    width: 720px;
    margin: 0;
    text-align: center;
    font-family: "Bebas Neue", "Oswald", sans-serif;
    font-weight: 400;
    font-size: 57px;
    line-height: 57px;
    letter-spacing: 2px;
    color: var(--ink);
    text-shadow: 3px 3px 0 var(--shadow);
  }
</style>
</head>
<body>
  <main class="cover">
    <div class="cover__art" role="img" aria-label="Night photograph of a starry sky over a dark island shoreline, with a warm glow behind the hills and calm water"></div>
    <h1 class="cover__title">
      <span>Beyond</span>
      <span>The Grey</span>
      <span>Harbor</span>
    </h1>
    <p class="cover__author">Derek Falloway</p>
  </main>
</body>
</html>
```